Quillbrookes websites redesign

Www.quill-brookes.com needs to be redesigned along with updations. The incremental material will be provided for the updations. We are looking for complete redesign of the pages with the new content. The complete write up will be provided soon

Target Market(s)

Global

Coding

Coded - Design and coding required

Number of Pages Required

5+ page

Requirements
Must have
• A clean and slick design for the Consulting.
Should not have
• Too many pictures which reduces the speed of the site

```html
<!DOCTYPE html>
<html lang="en">
<head>
<meta charset="utf-8">
<title>Quillbrookes Consultancy</title>
<link href="https://fonts.googleapis.com/css2?family=Roboto:wght@300;400;500&display=swap" rel="stylesheet">
<style>
:root{
  --maroon:#6b1f1f;
  --maroon-btn:#6e2424;
  --blue:#3a9fcf;
  --sky:#45b4dc;
  --ink:#2b2f3a;
  --body:#444;
  --muted:#666;
  --line:#e6e6e6;
  --white:#fff;
}
*{margin:0;padding:0;box-sizing:border-box}
html,body{width:754px;height:1200px;overflow:hidden;background:var(--white)}
body{font-family:'Roboto',sans-serif;color:var(--body);position:relative}
.site{position:relative;width:754px;height:1200px;overflow:hidden}

/* header */
.header{position:absolute;left:0;top:0;width:754px;height:53px;background:var(--white);border-bottom:1px solid var(--line)}
.brand{position:absolute;left:46px;top:12px;display:flex;align-items:center;gap:8px}
.brand-dot{width:28px;height:28px;border-radius:50%;background:var(--maroon)}
.brand-name{font-size:22px;font-weight:400;color:var(--ink);letter-spacing:.2px}
.nav{position:absolute;top:27px;left:0;font-size:8px;letter-spacing:.3px;color:var(--ink)}
.nav a{position:absolute;white-space:nowrap;text-decoration:none;color:inherit}
.nav .active{color:var(--blue);border-bottom:1.5px solid var(--blue);padding-bottom:4px}
.nav-sep{position:absolute;left:686px;top:16px;width:1px;height:26px;background:var(--line)}
.search{position:absolute;left:695px;top:26px}

/* hero */
.hero{position:absolute;left:0;top:53px;width:754px;height:295px;background:linear-gradient(90deg,#cfcfcf,#e6e6e6 45%,#d7d7d7)}
.hero-photo{position:absolute;left:330px;top:0;width:424px;height:295px;background:linear-gradient(135deg,#c9c9c9 0%,#3f9a3a 35%,#e9c530 60%,#c74343 85%,#eee 100%);opacity:.9}
.hero-title{position:absolute;left:47px;top:76px;font-size:27px;font-weight:400;line-height:28px;color:var(--maroon)}
.hero-text{position:absolute;left:47px;top:144px;width:300px;font-size:9.5px;line-height:14px;color:#333;text-align:justify}
.dots{position:absolute;left:47px;top:203px;display:flex;gap:4px}
.dots span{width:9px;height:9px;border-radius:50%;background:var(--white)}
.dots span.on{background:var(--maroon)}

/* about */
.about{position:absolute;left:0;top:348px;width:754px;height:208px;text-align:center}
.section-title{font-size:17px;font-weight:400;color:var(--ink);letter-spacing:.2px}
.section-title em{font-style:normal;color:var(--blue)}
.about .section-title{position:absolute;top:36px;width:100%}
.about-copy{position:absolute;left:70px;top:68px;width:614px;font-size:8.3px;line-height:12.8px;color:var(--muted)}
.about-copy p+p{margin-top:12.8px}
.btn{display:inline-block;background:var(--maroon-btn);color:var(--white);font-size:8.5px;letter-spacing:.3px;text-align:center;border-radius:1px}
.about .btn{position:absolute;left:336px;top:157px;width:82px;height:22px;line-height:22px}

/* stats */
.stats{position:absolute;left:0;top:556px;width:754px;height:226px;background:radial-gradient(ellipse at 30% 30%,#6a5a4a 0%,#2e2f38 55%,#1c1f28 100%)}
.stats-title{position:absolute;top:34px;width:100%;text-align:center;color:var(--white);font-size:16px;font-weight:400}
.stats-title small{font-size:10px}
.stats svg{position:absolute;left:0;top:0}
.stat-label{position:absolute;top:126px;width:120px;text-align:center;color:var(--white);font-size:17px;font-weight:400}

/* news */
.news{position:absolute;left:0;top:782px;width:754px;height:234px}
.news .section-title{position:absolute;left:47px;top:42px}
.arrows{position:absolute;left:664px;top:42px;display:flex;gap:3px}
.arrows span{width:19px;height:16px;display:flex;align-items:center;justify-content:center}
.arrows .prev{background:var(--blue)}
.arrows .next{background:var(--ink)}
.post{position:absolute;top:80px;width:202px}
.post-date{display:flex;align-items:center;gap:6px;font-size:18px;font-weight:300;color:var(--blue)}
.post-title{margin-top:5px;font-size:11.2px;font-weight:500;color:#222;letter-spacing:.5px}
.post-text{margin-top:8px;font-size:8px;line-height:12.8px;color:var(--muted);text-align:justify}
.post .btn{margin-top:11px;width:82px;height:21px;line-height:21px}

/* footer */
.footer{position:absolute;left:0;top:1016px;width:754px;height:184px;background:var(--sky);color:var(--white)}
.footer h3{position:absolute;top:33px;font-size:12.5px;font-weight:400;letter-spacing:.3px}
.email-field{position:absolute;left:47px;top:66px;width:152px;font-size:8.5px;border-bottom:1px solid var(--white);padding-bottom:4px}
.subscribe{position:absolute;left:47px;top:91px;width:152px;height:23px;line-height:23px;background:var(--maroon-btn);text-align:center;font-size:9.5px}
.contact-row{position:absolute;left:274px;display:flex;gap:8px;font-size:8.3px;line-height:12.5px}
.contact-row svg{flex:none;margin-top:1px}
.socials{position:absolute;left:515px;top:62px;display:flex;gap:3px}
.socials span{width:27px;height:27px;border:1px solid var(--white);border-radius:50%}
.copyright{position:absolute;left:517px;top:112px;font-size:8.3px;line-height:12.5px}
</style>
</head>
<body>
<div class="site">

  <header class="header">
    <div class="brand"><span class="brand-dot"></span><span class="brand-name">Quillbrookes</span></div>
    <nav class="nav">
      <a class="active" style="left:296px">HOME</a>
      <a style="left:354px">FOUNDER</a>
      <a style="left:414px">CONSULTANCY</a>
      <a style="left:495px">SYSTEM</a>
      <a style="left:550px">CASE STUDIES</a>
      <a style="left:632px">CONTACT</a>
    </nav>
    <span class="nav-sep"></span>
    <svg class="search" width="10" height="10" viewBox="0 0 10 10"><circle cx="4" cy="4" r="3" fill="none" stroke="#2b2f3a" stroke-width="1.5"/><line x1="6.2" y1="6.2" x2="9.2" y2="9.2" stroke="#2b2f3a" stroke-width="1.6"/></svg>
  </header>

  <section class="hero">
    <div class="hero-photo" role="img" aria-label="Photo of young sports fans with national flags painted on their faces, in front of a dotted world map"></div>
    <h1 class="hero-title">Nam libero tempore,<br>cum soluta</h1>
    <p class="hero-text">Quillbrookes Consultancy Limited capitalizes on synergies arising from trade and investment linkages between countries and knowledge of traditional and non-traditional pools of liquidity</p>
    <div class="dots"><span class="on"></span><span></span><span></span><span></span></div>
  </section>

  <section class="about">
    <h2 class="section-title">ABOUT <em>QUILLBROOKES CONSULTANCY</em></h2>
    <div class="about-copy">
      <p>Quillbrookes Consultancy Limited capitalizes on synergies arising from trade and investment linkages between countries and knowledge of traditional and non-traditional pools of liquidity to provide consultancy services to Emerging country banks, Corporates and SMEs.</p>
      <p>The Consultancy provides bank neutral views to Corporates and SMEs in Asian emerging markets and helps in improving financial structure and efficient use of funds. Our endeavor is to provide a distinct bottom line advantage to our clients. The primary focus is in regionalisation of the banking relationship across the globe, providing structured finance solutions and off balance sheet solutions.</p>
    </div>
    <a class="btn">LEARN MORE</a>
  </section>

  <section class="stats" role="img" aria-label="Blurred city lights at night as background">
    <h2 class="stats-title">WORLD MERCHANDISING TRADE 2012 <small>(USD BILLION)</small></h2>
    <svg width="754" height="226" viewBox="0 0 754 226" fill="none" stroke-width="3">
      <g stroke="rgba(255,255,255,.3)">
        <circle cx="122" cy="136" r="57"/><circle cx="292" cy="136" r="57"/>
        <circle cx="462" cy="136" r="57"/><circle cx="628" cy="136" r="57"/>
      </g>
      <g stroke="#fff" transform="rotate(-90 0 0)">
        <circle cx="-136" cy="122" r="57" stroke-dasharray="268 358"/>
        <circle cx="-136" cy="292" r="57" stroke-dasharray="110 358"/>
        <circle cx="-136" cy="462" r="57" stroke-dasharray="300 358"/>
        <circle cx="-136" cy="628" r="57" stroke-dasharray="345 358"/>
      </g>
    </svg>
    <div class="stat-label" style="left:62px">0-250</div>
    <div class="stat-label" style="left:232px">250-500</div>
    <div class="stat-label" style="left:402px">500-1000</div>
    <div class="stat-label" style="left:568px">&gt;1000</div>
  </section>

  <section class="news">
    <h2 class="section-title">LATEST <em>NEWS</em></h2>
    <div class="arrows">
      <span class="prev"><svg width="6" height="8" viewBox="0 0 6 8"><path d="M4.5 1 1.5 4l3 3" fill="none" stroke="#fff" stroke-width="1.2"/></svg></span>
      <span class="next"><svg width="6" height="8" viewBox="0 0 6 8"><path d="M1.5 1l3 3-3 3" fill="none" stroke="#fff" stroke-width="1.2"/></svg></span>
    </div>

    <article class="post" style="left:47px">
      <div class="post-date"><svg width="16" height="15" viewBox="0 0 16 15"><rect x="1" y="2" width="14" height="12" fill="none" stroke="#3a9fcf" stroke-width="1.3"/><rect x="1" y="2" width="14" height="3" fill="#3a9fcf"/><path d="M4 0v3M12 0v3M1 8h14M1 11h14M5 5v9M8 5v9M11 5v9" stroke="#3a9fcf" stroke-width="1"/></svg>25/05/2015</div>
      <h3 class="post-title">ESTABLISHING YOUR BRAND</h3>
      <p class="post-text">Sed ut perspiciatis unde omnis iste natus error sit voluptatem accusantium doloremque laudantium totam rem aperiam, eaque ipsa.</p>
      <a class="btn">LEARN MORE</a>
    </article>

    <article class="post" style="left:277px">
      <div class="post-date"><svg width="16" height="15" viewBox="0 0 16 15"><rect x="1" y="2" width="14" height="12" fill="none" stroke="#3a9fcf" stroke-width="1.3"/><rect x="1" y="2" width="14" height="3" fill="#3a9fcf"/><path d="M4 0v3M12 0v3M1 8h14M1 11h14M5 5v9M8 5v9M11 5v9" stroke="#3a9fcf" stroke-width="1"/></svg>25/05/2015</div>
      <h3 class="post-title">ESTABLISHING YOUR BRAND</h3>
      <p class="post-text">Sed ut perspiciatis unde omnis iste natus error sit voluptatem accusantium doloremque laudantium totam rem aperiam, eaque ipsa.</p>
      <a class="btn">LEARN MORE</a>
    </article>

    <article class="post" style="left:502px">
      <div class="post-date"><svg width="16" height="15" viewBox="0 0 16 15"><rect x="1" y="2" width="14" height="12" fill="none" stroke="#3a9fcf" stroke-width="1.3"/><rect x="1" y="2" width="14" height="3" fill="#3a9fcf"/><path d="M4 0v3M12 0v3M1 8h14M1 11h14M5 5v9M8 5v9M11 5v9" stroke="#3a9fcf" stroke-width="1"/></svg>25/05/2015</div>
      <h3 class="post-title">ESTABLISHING YOUR BRAND</h3>
      <p class="post-text">Sed ut perspiciatis unde omnis iste natus error sit voluptatem accusantium doloremque laudantium totam rem aperiam, eaque ipsa.</p>
      <a class="btn">LEARN MORE</a>
    </article>
  </section>

  <footer class="footer">
    <h3 style="left:47px">SIGN UP FOR UPDATES</h3>
    <div class="email-field">Email</div>
    <div class="subscribe">Subscribe</div>

    <h3 style="left:274px">FIND US</h3>
    <div class="contact-row" style="top:65px">
      <svg width="9" height="11" viewBox="0 0 9 11"><path d="M4.5 0C2 0 0 2 0 4.4 0 7.5 4.5 11 4.5 11S9 7.5 9 4.4C9 2 7 0 4.5 0z" fill="#fff"/><circle cx="4.5" cy="4.3" r="1.7" fill="#45b4dc"/></svg>
      <span>27 Harrow Lane, Eastmere<br>Northvale, EM4 2QT.</span>
    </div>
    <div class="contact-row" style="top:103px">
      <svg width="11" height="11" viewBox="0 0 11 11"><rect x="0" y="2" width="11" height="9" rx="1" fill="#fff"/><rect x="3" y="0" width="5" height="4" fill="#fff"/><rect x="2" y="5" width="7" height="2" fill="#45b4dc"/></svg>
      <span>Telephone: +1 555 014 2270<br>FAX: + 1 555 018 3391</span>
    </div>
    <div class="contact-row" style="top:143px">
      <svg width="10" height="8" viewBox="0 0 10 8"><rect width="10" height="8" fill="#fff"/><path d="M0 0l5 4.5L10 0" fill="none" stroke="#45b4dc" stroke-width="1"/></svg>
      <span>E-mail: hello@quillbrookes.example</span>
    </div>

    <h3 style="left:514px">KEEP IN TOUCH</h3>
    <div class="socials"><span></span><span></span><span></span><span></span><span></span></div>
    <p class="copyright">© Quillbrookes Consultancy Limited,<br>All Right Reserved.</p>
  </footer>

</div>
</body>
</html>
```